Visit card

Industry/Entity Type

Health Care

Contact Information for Business Card

O VITALIS SYSTEMS
Odile Brevard - chef de Projet

Requirements
Must have
• 318 Gaston Lemaire Street 59710 BÉTHUNE Tel: 33 (0) 327 481 605 Mobile: 06 42 19 37 64 Web: www.quorvexsystems.example Contact: o.brevard@o-vitalissystems.example
Should not have
• Respect for color

```html
<!DOCTYPE html>
<html lang="fr">
<head>
<meta charset="utf-8">
<title>O Vitalis Systems – Carte de visite</title>
<link rel="stylesheet" href="https://fonts.googleapis.com/css2?family=Lato:wght@400;700&display=swap">
<style>
  :root {
    --stage: #dcd9d5;
    --card: #f2f0ed;
    --card-edge: #e2dfdb;
    --ink: #3a3a3a;
    --ink-soft: #5e5e5e;
    --accent: #d3262c;
    --mark: #3b3b3b;
  }
  * { margin: 0; padding: 0; box-sizing: border-box; }
  html, body {
    width: 1200px; height: 1047px; overflow: hidden;
    background: var(--stage);
    font-family: "Lato", Arial, sans-serif;
  }
  .card {
    position: absolute; left: 100px; top: 252px;
    width: 1000px; height: 543px;
    background: var(--card);
    border: 1px solid var(--card-edge);
    border-radius: 22px;
    overflow: hidden;
    box-shadow: 0 12px 40px rgba(0,0,0,.12);
  }
  .accent-band {
    position: absolute; right: 0; top: 0;
    width: 280px; height: 100%;
    background: var(--accent);
  }
  .emblem {
    position: absolute; left: 469px; top: 20px;
    width: 502px; height: 502px;
  }
  .brand {
    position: absolute; left: 40px; top: 44px;
    display: flex; align-items: center; gap: 18px;
  }
  .brand-dot {
    width: 84px; height: 84px; border-radius: 50%;
    background: var(--mark);
  }
  .brand-name {
    font-weight: 700; font-size: 30px; letter-spacing: 1px;
    color: var(--ink);
  }
  .person { position: absolute; left: 40px; top: 190px; }
  .person-name {
    font-weight: 700; font-size: 32px; letter-spacing: .5px;
    color: var(--accent);
  }
  .person-role {
    margin-top: 6px; font-size: 22px; color: var(--ink-soft);
  }
  .address {
    position: absolute; left: 40px; top: 296px;
    font-size: 22px; line-height: 33px; color: var(--ink-soft);
    font-style: normal;
  }
  .contacts {
    position: absolute; left: 40px; top: 386px;
    list-style: none; font-size: 21px; color: var(--ink-soft);
  }
  .contacts li {
    display: flex; align-items: center; gap: 12px;
    height: 33px;
  }
  .contacts svg { width: 16px; height: 16px; flex: none; }
  .icon { fill: none; stroke: var(--accent); stroke-width: 2; }
  .icon-solid { fill: var(--accent); }
</style>
</head>
<body>
  <div class="card">
    <div class="accent-band"></div>
    <svg class="emblem" viewBox="0 0 502 502" aria-hidden="true">
      <circle cx="251" cy="251" r="251" fill="var(--mark)"/>
    </svg>

    <div class="brand">
      <span class="brand-dot"></span>
      <span class="brand-name">O VITALIS SYSTEMS</span>
    </div>

    <div class="person">
      <div class="person-name">ODILE BREVARD</div>
      <div class="person-role">Chef de Projet</div>
    </div>

    <address class="address">
      318 Rue Gaston Lemaire<br>
      59710 BÉTHUNE
    </address>

    <ul class="contacts">
      <li>
        <svg viewBox="0 0 16 16"><path class="icon-solid" d="M3 1l3 3-2 2c1 2 3 4 5 5l2-2 3 3-2 3C7 15 1 9 0 4z"/></svg>
        +33 (0) 327 481 605
      </li>
      <li>
        <svg viewBox="0 0 16 16"><rect class="icon" x="4" y="1" width="8" height="14" rx="1.5"/><circle class="icon-solid" cx="8" cy="12.5" r="1"/></svg>
        06 42 19 37 64
      </li>
      <li>
        <svg viewBox="0 0 16 16"><circle class="icon" cx="8" cy="8" r="6.5"/><ellipse class="icon" cx="8" cy="8" rx="3" ry="6.5"/><path class="icon" d="M1.5 8h13"/></svg>
        www.quorvexsystems.example
      </li>
      <li>
        <svg viewBox="0 0 16 16"><rect class="icon" x="1" y="3" width="14" height="10" rx="1"/><path class="icon" d="M1 4l7 5 7-5"/></svg>
        o.brevard@o-vitalissystems.example
      </li>
    </ul>
  </div>
</body>
</html>
```